Responsive OnePage Design for recruitment company

Quorvale is a modern company that sources interim people for its customers. Mostly developers, scrum master, project managers and designers. In this website we want to tell something about us, about how we work, our customers and we want our candidates be able to subscribe. The subscription form should be several fields (name, surname, email address, phone number and the possibility to upload your resume.We want it to fit into a existing wordpress plugin. We also want a listing of our job opportunities. The listing should be designed in a clear readable overview and if you click on the job you should get the details and be able to respond quickly by filling in you name, surname, email address, rate, phone number and upload your resume. We want this to be a standard configurable plugin. It should be easy to fill in the jobs in Wordpress by our administrator. We want a fresh, modern and cool design. It should be a responsive onepage design. If you click on a listed job you should stay on the same page. Our logo is added.

Target Market(s)

recruitment

Industry/Entity Type

Recruitment

Font styles to use
Sans Serif

Colors

Designer to choose colors to be used in the design.

Requirements
Must have
• Onepage design
• listing of job opportunities
• subscription forms
• be responsive

```html
<!DOCTYPE html>
<html lang="en">
<head>
<meta charset="utf-8">
<title>Quorvale – Interim Recruitment</title>
<link href="https://fonts.googleapis.com/css2?family=Lato:wght@400;700;900&family=Open+Sans:wght@400;600&display=swap" rel="stylesheet">
<style>
:root{
  --ink:#2e2f3a;
  --muted:#6b6f7c;
  --brand:#1565b8;
  --brand-dark:#0b3f8c;
  --hero-bg:#e8ebf6;
  --soft-bg:#eef1f6;
  --line:#d6d9e2;
  --white:#ffffff;
  --logo-grey:#9ea2aa;
}
*{margin:0;padding:0;box-sizing:border-box}
html,body{width:1200px;height:3448px;overflow:hidden}
body{font-family:'Lato',sans-serif;color:var(--ink);background:var(--white);position:relative}
.abs{position:absolute}
.center{text-align:center}

/* header */
.site-header{top:0;left:0;width:1200px;height:100px}
.brand{left:161px;top:28px;font-size:30px;font-weight:400;letter-spacing:8px;color:var(--ink);text-transform:uppercase}
.main-nav{left:527px;top:37px;display:flex;gap:22px;font-size:15px;font-weight:700;color:var(--ink)}

/* hero */
.hero{top:0;left:0;width:1200px;height:635px;background:var(--hero-bg);z-index:-1}
.hero-title{top:138px;left:0;width:1200px;font-size:36px;font-weight:900;line-height:43px;letter-spacing:.5px}
.hero-title span{color:var(--brand)}
.hero-art{left:180px;top:238px;width:840px;height:397px;background:linear-gradient(180deg,#f5f6fb 0%,#dfe3f0 100%);border-radius:4px 4px 0 0}
.btn-solid{display:flex;align-items:center;justify-content:center;background:var(--brand);color:var(--white);font-size:16px;font-weight:700;border-radius:22px}
.hero-btn{left:513px;top:239px;width:152px;height:42px;z-index:2}
.slide-arrow{width:58px;height:58px;border-radius:50%;background:#7eaedb;display:flex;align-items:center;justify-content:center}
.hero-prev{left:130px;top:309px}
.hero-next{left:1001px;top:309px}

/* about */
.about-art{left:97px;top:747px;width:490px;height:353px;background:radial-gradient(ellipse at 55% 55%,#cfd8f3 0%,#e7ecfa 55%,#ffffff 80%)}
.about-title{left:616px;top:768px;font-size:33px;font-weight:700;line-height:36px}
.about-title span{color:var(--brand);letter-spacing:1px}
.about-text{left:616px;top:856px;width:430px;font-family:'Open Sans',sans-serif;font-size:14.5px;line-height:23px;color:var(--muted)}
.about-text p+p{margin-top:20px}
.btn-outline{display:flex;align-items:center;justify-content:center;border:2px solid var(--brand);color:var(--brand);border-radius:24px;font-size:18px;font-weight:700}
.about-btn{left:616px;top:1042px;width:168px;height:48px}

/* how we work */
.how{top:1235px;left:0;width:1200px;height:495px;background:var(--soft-bg)}
.section-title{left:0;width:1200px;font-size:31px;font-weight:900;letter-spacing:1px}
.how .section-title{top:58px}
.step{width:290px;top:0}
.step-label{font-size:15px;font-weight:900;letter-spacing:1px}
.step-name{font-size:20px;line-height:24px;margin-top:6px}
.step-text{font-family:'Open Sans',sans-serif;font-size:14.5px;line-height:22px;color:var(--muted);margin-top:8px}

/* jobs */
.jobs{top:1730px;left:0;width:1200px;height:655px;background:linear-gradient(135deg,#1678c8 0%,#0c4d9c 60%,#083d8a 100%)}
.jobs .section-title{top:70px;color:var(--white)}
.job-card{width:435px;height:99px;background:rgba(255,255,255,.12);color:var(--white);padding:24px 0 0 32px}
.job-card.is-active{background:linear-gradient(180deg,#ffffff 0%,#e3e5ea 100%);color:var(--brand)}
.job-title{font-size:19px;line-height:26px}
.job-company{font-size:12px;margin-top:6px;opacity:.85}
.job-meta{position:absolute;top:30px;left:196px;display:flex;gap:18px;font-size:13.5px;align-items:center}
.job-meta span{display:flex;align-items:center;gap:6px}
.job-card.is-active .job-meta{color:var(--ink)}
.jobs-btn{left:508px;top:534px;width:175px;height:50px;border:2px solid var(--white);color:var(--white);border-radius:26px;font-size:19px;display:flex;align-items:center;justify-content:center}

/* customers */
.customers .section-title{top:2456px}
.client{width:170px;text-align:center;font-size:20px;font-weight:900;color:var(--logo-grey);display:flex;align-items:center;justify-content:center;gap:8px}
.client i{display:inline-block;width:14px;height:14px;background:var(--logo-grey)}
.client b{display:inline-block;width:16px;height:16px;border-radius:50%;background:var(--logo-grey)}

/* subscribe */
.subscribe{top:2859px;left:0;width:1200px;height:494px;background:linear-gradient(180deg,#e9ecf3 0%,#f4f5f8 50%,#e6e9f0 100%)}
.subscribe-title{top:62px;left:0;width:1200px;font-size:31px;font-weight:900;line-height:37px;letter-spacing:1px}
.subscribe-title span{color:var(--brand)}
.field{width:366px;height:54px;background:var(--white);border:1px solid var(--line);font-size:16px;display:flex;align-items:center;padding-left:24px;color:var(--ink)}
.field-upload{justify-content:space-between;padding-right:18px}
.btn-subscribe{width:366px;height:54px;background:linear-gradient(180deg,#1c6fc2 0%,#0b4391 100%);color:var(--white);font-size:18px;font-weight:900;display:flex;align-items:center;justify-content:center;letter-spacing:.5px}

/* footer */
.site-footer{top:3353px;left:0;width:1200px;height:95px;background:var(--white)}
.footer-brand{left:170px;top:30px;font-size:26px;letter-spacing:7px;text-transform:uppercase}
.copyright{left:501px;top:38px;font-size:14px;color:var(--ink)}
.social{top:28px;width:32px;height:32px;border-radius:50%;background:var(--brand)}
</style>
</head>
<body>

<div class="abs hero"></div>
<header class="abs site-header">
  <div class="abs brand">Quorvale</div>
  <nav class="abs main-nav"><span>ABOUT US</span><span>HOW IT WORKS</span><span>JOBS</span><span>CUSTOMERS</span><span>SUBSCRIBE</span></nav>
</header>

<section>
  <h1 class="abs hero-title center">WE SOURCES <span>INTERIM PEOPLE</span><br><span>FOR OUR CUSTOMERS</span></h1>
  <div class="abs hero-art" role="img" aria-label="Illustration of a team working together around an office desk with laptops"></div>
  <div class="abs btn-solid hero-btn">Read More</div>
  <div class="abs slide-arrow hero-prev"><svg width="18" height="18" viewBox="0 0 18 18"><path d="M11 3 5 9l6 6" fill="none" stroke="#fff" stroke-width="2.5"/></svg></div>
  <div class="abs slide-arrow hero-next"><svg width="18" height="18" viewBox="0 0 18 18"><path d="M7 3l6 6-6 6" fill="none" stroke="#fff" stroke-width="2.5"/></svg></div>
</section>

<section>
  <div class="abs about-art" role="img" aria-label="Illustration of recruiters reviewing candidate profiles on a large clipboard"></div>
  <h2 class="abs about-title">ABOUT<br><span>QUORVALE</span></h2>
  <div class="abs about-text">
    <p>Pellentesque faucibus Ut accumsan ultricies elit Maecenas at justo id velit placerat molestie Donec dictum lectus non odio Cras a ante vitae enim iaculis aliquam Mauris nunc quam venenatis nec euismod sit amet egestas placerat</p>
    <p>Ut ante enim dapibus malesuada fringilla eu condimentum quis tellus Aenean porttitor eros vel dolor Donec convallis</p>
  </div>
  <div class="abs btn-outline about-btn">Read More</div>
</section>

<section class="abs how">
  <svg class="abs" style="left:580px;top:0" width="40" height="16" viewBox="0 0 40 16"><path d="M0 0h40L20 16z" fill="#fff"/><path d="M14 4l6 5 6-5" fill="none" stroke="#9aa0ad" stroke-width="1.5"/></svg>
  <h2 class="abs section-title center">HOW WE WORK</h2>
  <svg class="abs" style="left:0;top:140px" width="1200" height="150" viewBox="0 0 1200 150">
    <g fill="none" stroke="#2e2f3a" stroke-width="2">
      <path d="M364 58c50-25 100-15 150 10" stroke-dasharray="3 5"/>
      <path d="M674 78c50 30 110 25 160-5" stroke-dasharray="3 5"/>
      <circle cx="300" cy="74" r="62"/><circle cx="612" cy="74" r="62"/><circle cx="935" cy="74" r="62"/>
    </g>
    <g fill="none" stroke="#1565b8" stroke-width="4" stroke-linecap="round" stroke-linejoin="round">
      <path d="M212 46l18-12v80"/>
      <rect x="272" y="52" width="56" height="38" rx="4"/><path d="M290 100h20M300 90v10"/>
      <path d="M520 54c4-18 42-18 42 2 0 16-44 36-44 58h46"/>
      <circle cx="608" cy="70" r="16"/><path d="M620 82l16 16"/>
      <path d="M838 40c8-12 40-12 40 6 0 12-12 18-22 18 12 0 24 6 24 20 0 20-36 22-44 6"/>
      <circle cx="940" cy="74" r="26"/><path d="M928 74l9 9 16-18"/>
    </g>
    <g fill="#2e2f3a"><circle cx="265" cy="30" r="5"/><circle cx="580" cy="34" r="5"/><circle cx="897" cy="28" r="5"/><circle cx="232" cy="114" r="4"/><circle cx="564" cy="114" r="4"/><circle cx="866" cy="110" r="4"/></g>
  </svg>
  <div class="abs step center" style="left:155px;top:296px"><div class="step-label">STEP 1</div><div class="step-name">Sign Up Free &amp; Create<br>Account</div><div class="step-text">Afringilla eu condimentum quis<br>tellus Aenean porttitor</div></div>
  <div class="abs step center" style="left:467px;top:296px"><div class="step-label">STEP 2</div><div class="step-name">Search Job</div><div class="step-text">Afringilla eu condimentum quis<br>tellus Aenean porttitor</div></div>
  <div class="abs step center" style="left:793px;top:296px"><div class="step-label">STEP 3</div><div class="step-name">Apply Now</div><div class="step-text">Afringilla eu condimentum quis<br>tellus Aenean porttitor</div></div>
</section>

<section class="abs jobs">
  <h2 class="abs section-title center">JOB OPPORTUNITIES</h2>
  <svg width="0" height="0" style="position:absolute"><defs>
    <symbol id="ico-clock" viewBox="0 0 16 16"><circle cx="8" cy="8" r="6.5" fill="none" stroke="currentColor" stroke-width="1.8"/><path d="M8 4v4l3 2" fill="none" stroke="currentColor" stroke-width="1.8"/></symbol>
    <symbol id="ico-pin" viewBox="0 0 16 16"><path d="M8 1a5 5 0 0 0-5 5c0 4 5 9 5 9s5-5 5-9a5 5 0 0 0-5-5zm0 7a2 2 0 1 1 0-4 2 2 0 0 1 0 4z" fill="currentColor"/></symbol>
  </defs></svg>
  <div class="abs job-card is-active" style="left:163px;top:144px"><div class="job-title">Job Title here</div><div class="job-company">Company Name</div><div class="job-meta"><span><svg width="16" height="16"><use href="#ico-clock"/></svg>Full Time</span><span><svg width="16" height="16"><use href="#ico-pin"/></svg>Location City</span></div></div>
  <div class="abs job-card" style="left:609px;top:144px"><div class="job-title">Programmer</div><div class="job-company">Company Name</div><div class="job-meta"><span><svg width="16" height="16"><use href="#ico-clock"/></svg>Full Time</span><span><svg width="16" height="16"><use href="#ico-pin"/></svg>Location City</span></div></div>
  <div class="abs job-card" style="left:163px;top:266px"><div class="job-title">Developer</div><div class="job-company">Company Name</div><div class="job-meta"><span><svg width="16" height="16"><use href="#ico-clock"/></svg>Full Time</span><span><svg width="16" height="16"><use href="#ico-pin"/></svg>Location City</span></div></div>
  <div class="abs job-card" style="left:609px;top:266px"><div class="job-title">Graphic Designer</div><div class="job-company">Company Name</div><div class="job-meta"><span><svg width="16" height="16"><use href="#ico-clock"/></svg>Full Time</span><span><svg width="16" height="16"><use href="#ico-pin"/></svg>Location City</span></div></div>
  <div class="abs job-card" style="left:163px;top:388px"><div class="job-title">Project Manager</div><div class="job-company">Company Name</div><div class="job-meta"><span><svg width="16" height="16"><use href="#ico-clock"/></svg>Full Time</span><span><svg width="16" height="16"><use href="#ico-pin"/></svg>Location City</span></div></div>
  <div class="abs job-card" style="left:609px;top:388px"><div class="job-title">Scrum master</div><div class="job-company">Company Name</div><div class="job-meta"><span><svg width="16" height="16"><use href="#ico-clock"/></svg>Full Time</span><span><svg width="16" height="16"><use href="#ico-pin"/></svg>Location City</span></div></div>
  <div class="abs jobs-btn">View More</div>
</section>

<section class="customers">
  <h2 class="abs section-title center">OUR CUSTOMERS</h2>
  <svg class="abs" style="left:96px;top:2596px" width="26" height="52" viewBox="0 0 26 52"><path d="M22 4 4 26l18 22" fill="none" stroke="#b5b9c2" stroke-width="2.5"/></svg>
  <svg class="abs" style="left:1076px;top:2596px" width="26" height="52" viewBox="0 0 26 52"><path d="M4 4l18 22L4 48" fill="none" stroke="#b5b9c2" stroke-width="2.5"/></svg>
  <div class="abs client" style="left:145px;top:2566px;height:36px"><b></b>Northvale</div>
  <div class="abs client" style="left:329px;top:2566px;height:36px"><i></i>Kestro</div>
  <div class="abs client" style="left:513px;top:2566px;height:36px">kindred care</div>
  <div class="abs client" style="left:697px;top:2566px;height:36px"><i></i>Alder Assure</div>
  <div class="abs client" style="left:881px;top:2566px;height:36px"><b></b>platewise</div>
  <div class="abs client" style="left:145px;top:2674px;height:36px"><b></b>Vireo</div>
  <div class="abs client" style="left:329px;top:2674px;height:36px">Tagline Co</div>
  <div class="abs client" style="left:513px;top:2674px;height:36px">OVAN</div>
  <div class="abs client" style="left:697px;top:2674px;height:36px">Fellside Mutual</div>
  <div class="abs client" style="left:881px;top:2674px;height:36px">Harlow</div>
</section>

<section class="abs subscribe" role="img" aria-label="Soft background photo of a bright workspace desk with laptop, notebook and phone">
  <svg class="abs" style="left:580px;top:0" width="40" height="16" viewBox="0 0 40 16"><path d="M0 0h40L20 16z" fill="#fff"/><path d="M14 4l6 5 6-5" fill="none" stroke="#9aa0ad" stroke-width="1.5"/></svg>
  <h2 class="abs subscribe-title center">SUBSCRIPTION<br><span>FORM</span></h2>
  <div class="abs field" style="left:228px;top:177px">First Name</div>
  <div class="abs field" style="left:607px;top:177px">Last Name</div>
  <div class="abs field" style="left:228px;top:245px">Email address</div>
  <div class="abs field" style="left:607px;top:245px">Phone Number</div>
  <div class="abs field field-upload" style="left:228px;top:313px">Upload Resume<svg width="22" height="22" viewBox="0 0 22 22"><path d="M3 13v6h16v-6M11 15V3M6 8l5-5 5 5" fill="none" stroke="#9aa0ad" stroke-width="1.6"/></svg></div>
  <div class="abs btn-subscribe" style="left:607px;top:313px">SUBSCRIBE</div>
</section>

<footer class="abs site-footer">
  <div class="abs footer-brand">Quorvale</div>
  <div class="abs copyright">© 2019 Company Name &nbsp;All right reserved</div>
  <div class="abs social" style="left:881px" aria-label="Social link 1"></div>
  <div class="abs social" style="left:920px" aria-label="Social link 2"></div>
  <div class="abs social" style="left:959px" aria-label="Social link 3"></div>
  <div class="abs social" style="left:998px" aria-label="Social link 4"></div>
</footer>

</body>
</html>
```